Copper Field Agency Website - Wordpress Web UPDATED BRIEF

FINAL LOGO UPLOADED - please look to this as reference for how we would like the site to look and feel.

We are a digital marketing agency - looking to have a new website built. We are looking for a simple one page feel of site that will allow us to grow it later. (Feel free to take some liberties with that if your imagination veers off) Must be very, playful, bold, sleek and easily integrate video. Wordpress only.

Overview:

Copper Field is a creative constellation. We are built on what's great about the shared economy. With access to thousands of content creators, designers, technicians, writers, strategists and other creatives around the world, we are built differently than a traditional “brick and mortar” Marketing Agency. We provide the traditional services our clients have come to expect, without the “5X factor” of covering the overhead common in the old agency model. We believe even better work can be created in collaboration with our clients and by passing those savings back to them for their use. Our clients pay for our art, our work and our passion –not our furniture.

"Copper Field, Let's Build Together"

Target Market(s)

companies looking for creative agency help, video production, creative consulting and coaching

Industry/Entity Type

Digital Marketing

Coding

Coded - Design and coding required

Number of Pages Required

1 page

Font styles to use
Sans Serif

Colors
3277b5
33a6d7
ec1f27

Requirements
Must have
• Wordpress design is a must. Looking for a one sheet homepage - with sections that are all on the main front page. We will have videos to embed, and should be able to have client logos and easy access to show a variety of our creative work.
• Please look to the logo for how we would like the site to feel.
• Please think "icon process flow" instead of blocks of text (which we used to have). Use the text to explain what the process flow should represent - don't actually copy paste the text but show it visually in icons.
Nice to have
• innovation around how we show video content. solid colors complementary to our palette and aesthetic.
Should not have
• Standard HTML coding

```html
<!DOCTYPE html>
<html lang="en">
<head>
<meta charset="utf-8">
<title>Copper Field Agency – Digital Marketing Agency</title>
<link href="https://fonts.googleapis.com/css2?family=Roboto:wght@400;500;700;900&display=swap" rel="stylesheet">
<style>
:root{
  --blue:#3277b5;
  --blue-dark:#1f5fa6;
  --sky:#33a6d7;
  --red:#ec1f27;
  --navy:#1d2a44;
  --text:#5c6470;
  --light:#eef3f9;
  --line:#dde3ea;
  --white:#ffffff;
}
*{box-sizing:border-box;margin:0;padding:0}
html,body{width:1200px;height:4872px;overflow:hidden}
body{font-family:"Roboto",Arial,sans-serif;color:var(--text);background:var(--white);position:relative}
section,header,footer{position:absolute;left:0;width:1200px}
.abs{position:absolute}
.btn{position:absolute;background:var(--red);color:var(--white);font-weight:700;font-size:14px;text-transform:uppercase;border-radius:24px;display:flex;align-items:center;justify-content:center;letter-spacing:.3px}
.section-title{position:absolute;left:0;width:1200px;text-align:center;font-size:36px;font-weight:700;color:var(--blue-dark);text-transform:uppercase}

/* header + hero */
.hero{top:0;height:680px;background:linear-gradient(180deg,#fff 0%,#f5f8fb 100%)}
.topbar-phone{left:160px;top:18px;display:flex;align-items:center;gap:12px;color:var(--red);font-weight:700;font-size:22px}
.phone-icon{width:30px;height:30px;border:2px solid var(--red);border-radius:50%;display:flex;align-items:center;justify-content:center}
.social{right:150px;top:16px;display:flex;gap:12px}
.social span{width:30px;height:30px;border:2px solid var(--blue);border-radius:50%}
.topbar-rule{left:150px;top:60px;width:900px;height:1px;background:var(--line)}
.nav{right:150px;top:68px;display:flex;gap:20px;font-size:15px;font-weight:500;color:var(--navy)}
.brand{display:flex;align-items:center;gap:18px}
.brand-dot{width:64px;height:64px;border-radius:50%;background:var(--blue);flex:none}
.brand-name{font-weight:900;color:var(--navy);letter-spacing:1px;white-space:nowrap}
.hero-brand{left:160px;top:340px}
.hero-brand .brand-name{font-size:52px}
.hero-arrow{left:60px;width:40px;height:40px;border:2px solid #b9c2cc;border-radius:50%;display:flex;align-items:center;justify-content:center}
.hero-title{left:640px;top:320px;font-size:44px;font-weight:900;line-height:48px;color:var(--blue-dark);text-transform:uppercase}
.hero-sub{left:640px;top:424px;font-size:20px;font-weight:700;line-height:24px;color:var(--navy)}

/* about */
.about{top:680px;height:520px;background:var(--light)}
.about-title{left:180px;top:110px;font-size:36px;font-weight:700;color:var(--blue-dark)}
.about-text{left:180px;top:175px;width:380px;font-size:14px;line-height:24px}
.about-text p{margin-bottom:18px}
.about-ring{left:650px;top:60px;width:420px;height:420px;border-radius:50%;border:8px solid var(--blue);background:var(--white);display:flex;align-items:center;justify-content:center}
.about-art{width:340px;height:340px;border-radius:50%;background:radial-gradient(circle,#f6c947 0%,#ef7a4d 35%,#5aa7dd 65%,#ffffff 100%)}

/* services */
.services{top:1200px;height:940px;background:var(--white)}
.services-intro{left:300px;top:192px;width:600px;text-align:center;font-size:14px;line-height:22px}
.service-grid{left:152px;top:292px;width:896px;display:grid;grid-template-columns:repeat(3,288px);gap:24px 16px}
.service-card{height:240px;border:1px solid var(--line);background:var(--white);text-align:center;padding:30px 30px 0;color:var(--text)}
.service-card.featured{background:var(--blue);border-color:var(--blue);color:#dfeaf6}
.service-icon{display:block;width:56px;height:56px;margin:0 auto 16px;color:var(--blue)}
.featured .service-icon{color:var(--white)}
.service-card h3{font-size:16px;font-weight:700;color:var(--navy);margin-bottom:12px}
.featured h3{color:var(--white)}
.service-card p{font-size:13px;line-height:20px}

/* videos */
.videos{top:2140px;height:700px}
.videos-wave{position:absolute;left:0;top:0}
.videos .section-title{top:82px;color:var(--white)}
.video-frame{left:200px;top:140px;width:800px;height:440px;background:linear-gradient(135deg,#6f7f8c 0%,#c7b9a4 45%,#4b5a68 100%)}
.play{left:560px;top:320px;width:82px;height:58px;background:var(--red);border-radius:14px;display:flex;align-items:center;justify-content:center}
.video-arrow{top:340px}

/* creative work */
.work{top:2840px;height:800px;background:var(--white)}
.work .section-title{top:52px}
.work-grid{left:152px;top:124px;width:896px;display:grid;grid-template-columns:repeat(3,284px);gap:22px 22px}
.work-tile{position:relative;height:236px}
.work-tile:nth-child(n+4){height:226px}
.work-label{position:absolute;left:0;bottom:0;width:100%;height:40px;background:rgba(31,95,166,.9);color:var(--white);font-size:13px;font-weight:700;display:flex;align-items:center;padding-left:14px}
.t1{background:linear-gradient(135deg,#2e3f52,#8aa0b5)}
.t2{background:linear-gradient(135deg,#3a6fa6,#9cc3e0)}
.t3{background:linear-gradient(135deg,#4a5361,#b3aba0)}
.t4{background:linear-gradient(135deg,#1e6aa8,#7fc2ea)}
.t5{background:linear-gradient(135deg,#2c3440,#7d8a98)}
.t6{background:linear-gradient(135deg,#6d7782,#d6d9dc)}

/* testimonials */
.testimonials{top:3640px;height:480px;background:var(--light)}
.testimonials .section-title{top:82px}
.quote-row{left:152px;top:152px;width:896px;display:grid;grid-template-columns:repeat(3,288px);gap:16px}
.quote-card{height:200px;background:var(--white);border-radius:10px;box-shadow:0 6px 18px rgba(40,70,110,.12);padding:26px 24px;font-size:13px;line-height:20px;position:relative}
.quote-mark{position:absolute;left:50%;bottom:22px;width:22px;height:14px;margin-left:-11px;background:#c9d2dc;border-radius:3px}
.person{display:flex;align-items:center;gap:12px;margin-top:26px;padding-left:10px;font-size:13px;line-height:18px;color:var(--navy)}
.avatar{width:50px;height:50px;border-radius:50%;background:linear-gradient(135deg,#9fb3c8,#5d7692);flex:none}
.t-arrow{top:232px;color:#7a8594}

/* clients */
.clients{top:4120px;height:280px;background:var(--white)}
.clients .section-title{top:92px}
.client-row{left:186px;top:172px;width:828px;display:flex;gap:36px}
.client{width:180px;height:68px;background:var(--white);box-shadow:0 4px 14px rgba(40,70,110,.12);display:flex;align-items:center;justify-content:center;font-size:20px;font-weight:700;color:var(--navy)}
.c-arrow{top:195px;color:#7a8594}

/* footer */
.footer{top:4400px;height:472px;background:var(--blue-dark);color:#cfe0f2}
.footer-brand{left:110px;top:150px}
.footer-brand .brand-dot{width:48px;height:48px;background:var(--sky)}
.footer-brand .brand-name{font-size:36px;color:var(--white)}
.footer-col{top:120px;font-size:13px;line-height:28px}
.footer-col h4{font-size:14px;font-weight:700;color:var(--white);text-transform:uppercase;margin-bottom:8px}
.footer-col ul{list-style:none}
.footer-col li::before{content:"›";margin-right:8px;color:var(--sky)}
.two-col{display:grid;grid-template-columns:110px 130px}
.copyright{left:0;top:416px;width:1200px;height:56px;border-top:1px solid rgba(255,255,255,.2);display:flex;justify-content:space-between;align-items:center;padding:0 150px;font-size:12px}
</style>
</head>
<body>

<header class="hero">
  <div class="abs topbar-phone">
    <span class="phone-icon"><svg width="14" height="14" viewBox="0 0 24 24"><path d="M6.6 10.8a15 15 0 0 0 6.6 6.6l2.2-2.2a1 1 0 0 1 1-.25 11.4 11.4 0 0 0 3.6.57 1 1 0 0 1 1 1V20a1 1 0 0 1-1 1A17 17 0 0 1 3 4a1 1 0 0 1 1-1h3.5a1 1 0 0 1 1 1c0 1.25.2 2.45.57 3.57a1 1 0 0 1-.25 1z" fill="#ec1f27"/></svg></span>
    +1 555 014 2290
  </div>
  <div class="abs social"><span></span><span></span><span></span><span></span></div>
  <div class="abs topbar-rule"></div>
  <nav class="abs nav">
    <span>Home</span><span>About</span><span>Services</span><span>Videos</span><span>Our Creative Work</span><span>Testimonials</span><span>Clients</span>
  </nav>

  <div class="abs brand hero-brand">
    <span class="brand-dot"></span>
    <span class="brand-name">COPPER FIELD</span>
  </div>

  <div class="abs hero-arrow" style="top:330px"><svg width="12" height="12" viewBox="0 0 12 12"><path d="M8 1 3 6l5 5" stroke="#8a95a2" stroke-width="2" fill="none"/></svg></div>
  <div class="abs hero-arrow" style="top:392px"><svg width="12" height="12" viewBox="0 0 12 12"><path d="M4 1l5 5-5 5" stroke="#8a95a2" stroke-width="2" fill="none"/></svg></div>

  <h1 class="abs hero-title">Digital<br>Marketing Agency</h1>
  <p class="abs hero-sub">We are passionate about creating with you,<br>not just for you.</p>
  <span class="btn" style="left:640px;top:488px;width:186px;height:42px">Connect with us</span>
</header>

<section class="about">
  <h2 class="abs about-title">ABOUT COPPER FIELD</h2>
  <div class="abs about-text">
    <p>A Creative Constellation is a network of writers, designers and creators brought together by Copper Field to support your campaign or project. After Discovery, your Copper Field Creative Director chooses from our roster of highly skilled Creatives, the most agency-ready team members for your vision, aesthetic and goals.</p>
    <p>What's better? A creative constellation is a living, animated creative team that can evolve as your needs change.</p>
  </div>
  <span class="btn" style="left:180px;top:392px;width:140px;height:38px;font-size:12px">More about us</span>
  <div class="abs about-ring"><div class="about-art" role="img" aria-label="Illustration of a team building charts and screens together"></div></div>
</section>

<section class="services">
  <h2 class="section-title" style="top:128px">COPPERFIELD SERVICES</h2>
  <p class="abs services-intro">Lorem ipsum dolor sit amet, consectetur adipiscing elit, sed do eiusmod tempor incididunt ut labore et dolore magna aliqua ut enim minim veniam, quis nostrud exercitation ullamco laboris nisi aliquip.</p>
  <div class="abs service-grid">
    <div class="service-card">
      <svg class="service-icon" viewBox="0 0 56 56" fill="none" stroke="currentColor" stroke-width="3" stroke-linecap="round"><circle cx="24" cy="24" r="14"/><path d="M34 34l14 14"/><path d="M18 24a6 6 0 0 1 6-6"/></svg>
      <h3>DISCOVERY</h3><p>Lorem ipsum dolor sit amet, consectetur adipiscing elit, sed eiusmod tempor incididunt ut labore dolore magna aliqua.</p></div>
    <div class="service-card featured">
      <svg class="service-icon" viewBox="0 0 56 56" fill="none" stroke="currentColor" stroke-width="3" stroke-linecap="round"><circle cx="28" cy="28" r="20"/><circle cx="28" cy="28" r="12"/><circle cx="28" cy="28" r="4" fill="currentColor"/></svg>
      <h3>STRATEGY</h3><p>Lorem ipsum dolor sit amet, consectetur adipiscing elit, sed eiusmod tempor incididunt ut labore dolore magna aliqua.</p></div>
    <div class="service-card">
      <svg class="service-icon" viewBox="0 0 56 56" fill="none" stroke="currentColor" stroke-width="3" stroke-linecap="round"><circle cx="28" cy="28" r="8"/><path d="M28 8v8M28 40v8M8 28h8M40 28h8M14 14l6 6M36 36l6 6M42 14l-6 6M20 36l-6 6"/></svg>
      <h3>PROJECT MANAGEMENT</h3><p>Lorem ipsum dolor sit amet, consectetur adipiscing elit, sed eiusmod tempor incididunt ut labore dolore magna aliqua.</p></div>
    <div class="service-card">
      <svg class="service-icon" viewBox="0 0 56 56" fill="none" stroke="currentColor" stroke-width="3" stroke-linejoin="round"><rect x="6" y="16" width="32" height="26" rx="3"/><path d="M38 24l12-7v22l-12-7z"/></svg>
      <h3>PRODUCTION</h3><p>Lorem ipsum dolor sit amet, consectetur adipiscing elit, sed eiusmod tempor incididunt ut labore dolore magna aliqua.</p></div>
    <div class="service-card">
      <svg class="service-icon" viewBox="0 0 56 56" fill="none" stroke="currentColor" stroke-width="3" stroke-linejoin="round" stroke-linecap="round"><path d="M8 22h8l20-12v36L16 34H8z"/><path d="M16 34l4 12h6l-3-11"/><path d="M44 22a8 8 0 0 1 0 12"/></svg>
      <h3>PAID MEDIA &amp; COACHING</h3><p>Lorem ipsum dolor sit amet, consectetur adipiscing elit, sed eiusmod tempor incididunt ut labore dolore magna aliqua.</p></div>
    <div class="service-card">
      <svg class="service-icon" viewBox="0 0 56 56" fill="none" stroke="currentColor" stroke-width="3" stroke-linejoin="round" stroke-linecap="round"><path d="M12 6h22l10 10v34H12z"/><path d="M34 6v10h10"/><path d="M19 26h18M19 33h18M19 40h12"/></svg>
      <h3>CONTENT</h3><p>Lorem ipsum dolor sit amet, consectetur adipiscing elit, sed eiusmod tempor incididunt ut labore dolore magna aliqua.</p></div>
  </div>
</section>

<section class="videos">
  <svg class="videos-wave" width="1200" height="700" viewBox="0 0 1200 700">
    <path d="M0 60 Q600 -40 1200 60 L1200 640 Q600 740 0 640 Z" fill="#1f5fa6"/>
  </svg>
  <h2 class="section-title">OUR VIDEOS</h2>
  <div class="abs video-frame" role="img" aria-label="Video still of a team working at a desk with laptops"></div>
  <div class="abs play"><svg width="24" height="26" viewBox="0 0 24 26"><path d="M2 1l21 12L2 25z" fill="#fff"/></svg></div>
  <svg class="abs video-arrow" style="left:90px" width="20" height="30" viewBox="0 0 20 30"><path d="M16 2 4 15l12 13" stroke="#fff" stroke-width="4" fill="none"/></svg>
  <svg class="abs video-arrow" style="left:1090px" width="20" height="30" viewBox="0 0 20 30"><path d="M4 2l12 13L4 28" stroke="#fff" stroke-width="4" fill="none"/></svg>
</section>

<section class="work">
  <h2 class="section-title">OUR CREATIVE WORK</h2>
  <div class="abs work-grid">
    <div class="work-tile t1" role="img" aria-label="Project photo of a laptop and coffee on a desk"><span class="work-label">LOREM IPSUM DOLOR</span></div>
    <div class="work-tile t2" role="img" aria-label="Project photo of a team meeting"><span class="work-label">LOREM IPSUM</span></div>
    <div class="work-tile t3" role="img" aria-label="Project photo of hands writing on paper"><span class="work-label">LOREM IPSUM DOLOR SITAS</span></div>
    <div class="work-tile t4" role="img" aria-label="Project photo of a digital interface"><span class="work-label">LOREM IPSUM</span></div>
    <div class="work-tile t5" role="img" aria-label="Project photo of a person using a laptop"><span class="work-label">LOREM IPSUM DOLOR SITAS</span></div>
    <div class="work-tile t6" role="img" aria-label="Project photo of charts on a tablet"><span class="work-label">LOREM IPSUM DOLOR</span></div>
  </div>
  <span class="btn" style="left:528px;top:678px;width:144px;height:40px;font-size:12px">View more work</span>
</section>

<section class="testimonials">
  <h2 class="section-title">TESTIMONIALS</h2>
  <svg class="abs t-arrow" style="left:96px" width="14" height="22" viewBox="0 0 14 22"><path d="M12 2 3 11l9 9" stroke="currentColor" stroke-width="3" fill="none"/></svg>
  <svg class="abs t-arrow" style="left:1090px" width="14" height="22" viewBox="0 0 14 22"><path d="M2 2l9 9-9 9" stroke="currentColor" stroke-width="3" fill="none"/></svg>
  <div class="abs quote-row">
    <div>
      <div class="quote-card">Copper Field is providing to be focus in the time from consulting statuses and we look forward to collaborating with them again in the future.<span class="quote-mark"></span></div>
      <div class="person"><span class="avatar" role="img" aria-label="Client portrait"></span><span>Marla Quinton,<br>Harbor Stage</span></div>
    </div>
    <div>
      <div class="quote-card">Throughout the planning and filming process, the Copper Field team was incredibly responsive to the input and needs of our staff.<span class="quote-mark"></span></div>
      <div class="person"><span class="avatar" role="img" aria-label="Client portrait"></span><span>Harbor Stage at the Linden Hall<br>Theatre</span></div>
    </div>
    <div>
      <div class="quote-card">Copper Field have helped us to focus, to develop our work clearly and to understand our aims, and continues our drive to achieve a vibrant work of art.<span class="quote-mark"></span></div>
      <div class="person"><span class="avatar" role="img" aria-label="Client portrait"></span><span>Wren Dance<br>Collective</span></div>
    </div>
  </div>
</section>

<section class="clients">
  <h2 class="section-title">OUR CLIENTS</h2>
  <svg class="abs c-arrow" style="left:96px" width="14" height="22" viewBox="0 0 14 22"><path d="M12 2 3 11l9 9" stroke="currentColor" stroke-width="3" fill="none"/></svg>
  <svg class="abs c-arrow" style="left:1090px" width="14" height="22" viewBox="0 0 14 22"><path d="M2 2l9 9-9 9" stroke="currentColor" stroke-width="3" fill="none"/></svg>
  <div class="abs client-row">
    <div class="client">Northgate</div>
    <div class="client">Tidewell</div>
    <div class="client">Brightmoor</div>
    <div class="client">Greenleaf</div>
  </div>
</section>

<footer class="footer">
  <div class="abs brand footer-brand">
    <span class="brand-dot"></span>
    <span class="brand-name">COPPER FIELD</span>
  </div>
  <div class="abs footer-col" style="left:500px">
    <h4>Quick Links</h4>
    <div class="two-col">
      <ul><li>Home</li><li>About</li><li>Services</li><li>Our Videos</li></ul>
      <ul><li>Creative Work</li><li>Testimonials</li><li>Our Clients</li><li>Contact Us</li></ul>
    </div>
  </div>
  <div class="abs footer-col" style="left:760px">
    <h4>Contact Us</h4>
    <ul><li>Copper Field</li><li>Lorem ipsum is Simple</li><li>hello@copperfield.example</li><li>+1 555 014 2290</li></ul>
  </div>
  <div class="abs footer-col" style="left:960px">
    <h4>Get Connected</h4>
    <ul><li>Pagebook</li><li>Chirper</li><li>Snapgram</li><li>Vidtube</li></ul>
  </div>
  <div class="abs copyright">
    <span>Copyright © 2019 Copper Field. All Rights Reserved</span>
    <span>Terms &amp; Conditions / Privacy Policy</span>
  </div>
</footer>

</body>
</html>
```